Brell Stone Company Business Cards

Front and Back Business Card - logo and text setup - cool design. I need workable photoshop or illustrator files so I can setup each employee card with design that is created
Updates

Hi everyone, thank you for the great entries. Please no more white and blue cards - there are so many already - black and silver only now please. thanks!

Target Market(s)

Construction Industry - Facility Managers

Industry/Entity Type

Construction

Contact Information for Business Card

I really like contemporary simplistic looks - clean neat....not opposed to seeing some black backrounds

Requirements
Must have
• Logo/website address with design on front only - www.brellstone-example.com (logo attached)
• Back:
• Name/Title/Company Address/Phone/email address
Nice to have
• Cool design
Should not have
• Nothing gimmicky like Fire or Water - since we are a Fire Protection company - it has all been done

```html
<!DOCTYPE html>
<html lang="en">
<head>
<meta charset="utf-8">
<title>Brell Stone Company Business Cards</title>
<link rel="stylesheet" href="https://fonts.googleapis.com/css2?family=Poppins:wght@400;600;700&display=swap">
<style>
  :root {
    --page-bg: #5b5c5e;
    --card-black: #1d1d1e;
    --silver: #9c9da0;
    --silver-light: #d4d5d7;
    --text-soft: #b3b4b6;
    --accent-red: #e8432b;
    --card-shadow: 0 14px 30px rgba(0, 0, 0, 0.35);
  }
  * { box-sizing: border-box; margin: 0; padding: 0; }
  html, body { width: 1200px; height: 857px; overflow: hidden; }
  body {
    background: var(--page-bg);
    font-family: "Poppins", Arial, sans-serif;
    position: relative;
  }
  .card {
    position: absolute;
    top: 292px;
    width: 490px;
    height: 280px;
    border-radius: 3px;
    background: var(--card-black);
    box-shadow: var(--card-shadow);
  }
  /* Front */
  .card-front {
    left: 80px;
    display: flex;
    flex-direction: column;
    align-items: center;
    justify-content: center;
  }
  .card-front .wordmark {
    font-weight: 700;
    font-size: 54px;
    letter-spacing: -1px;
    color: var(--silver);
    line-height: 1;
    margin-top: 18px;
    white-space: nowrap;
  }
  .card-front .website {
    margin-top: 58px;
    font-size: 13px;
    letter-spacing: 0.6px;
    color: var(--silver-light);
  }
  .card-front .website .brand { color: var(--accent-red); }
  /* Back */
  .card-back {
    left: 630px;
    display: flex;
    align-items: center;
    padding: 0 18px 0 24px;
  }
  .card-back .wordmark {
    flex: none;
    font-weight: 700;
    font-size: 32px;
    letter-spacing: -0.8px;
    line-height: 1;
    color: var(--silver);
    white-space: nowrap;
  }
  .divider {
    flex: none;
    width: 0;
    height: 150px;
    border-left: 2px dashed var(--accent-red);
    margin: 0 16px 0 14px;
  }
  .contact {
    color: var(--text-soft);
    font-size: 11.5px;
    line-height: 1.6;
    white-space: nowrap;
  }
  .contact .name {
    font-weight: 700;
    font-size: 15px;
    color: var(--silver-light);
    letter-spacing: 0.3px;
  }
  .contact .title { margin-bottom: 2px; }
  .contact .line { display: flex; align-items: center; gap: 7px; }
  .contact .icon { width: 10px; height: 10px; flex: none; fill: var(--accent-red); }
</style>
</head>
<body>
  <section class="card card-front" aria-label="Card front">
    <div class="wordmark">Brell Stone</div>
    <div class="website">www.<span class="brand">brellstone</span>-example.com</div>
  </section>

  <section class="card card-back" aria-label="Card back">
    <div class="wordmark">Brell Stone</div>
    <div class="divider"></div>
    <div class="contact">
      <div class="name">DANA WHITLOCK</div>
      <div class="title">Senior Consultant</div>
      <div>48 Harbor Lane</div>
      <div>Westfield, NY 10250</div>
      <div class="line">
        <svg class="icon" viewBox="0 0 24 24"><path d="M6.6 10.8a15 15 0 0 0 6.6 6.6l2.2-2.2a1 1 0 0 1 1-.25 11.4 11.4 0 0 0 3.6.57 1 1 0 0 1 1 1V20a1 1 0 0 1-1 1A17 17 0 0 1 3 4a1 1 0 0 1 1-1h3.5a1 1 0 0 1 1 1c0 1.25.2 2.45.57 3.57a1 1 0 0 1-.25 1z"/></svg>
        <span>(555) 014-2281</span>
      </div>
      <div class="line">
        <svg class="icon" viewBox="0 0 24 24"><path d="M6 3h12v5H6z"/><path d="M3 9h18v8h-3v4H6v-4H3zm5 6v4h8v-4z"/></svg>
        <span>(555) 014-2282</span>
      </div>
      <div class="line">
        <svg class="icon" viewBox="0 0 24 24"><path d="M2 5h20v14H2zm2 2v.5l8 5 8-5V7zm0 2.9V17h16V9.9l-8 5z"/></svg>
        <span>info@brellstone-example.com</span>
      </div>
      <div class="line">
        <svg class="icon" viewBox="0 0 24 24"><path d="M12 2a10 10 0 1 0 0 20 10 10 0 0 0 0-20zm6.9 6h-3a15 15 0 0 0-1.3-3.9A8 8 0 0 1 18.9 8zM12 4a13 13 0 0 1 1.9 4h-3.8A13 13 0 0 1 12 4zM4.3 14a8 8 0 0 1 0-4h3.4a16 16 0 0 0 0 4zm.8 2h3a15 15 0 0 0 1.3 3.9A8 8 0 0 1 5.1 16zm3-8h-3a8 8 0 0 1 4.3-3.9A15 15 0 0 0 8.1 8zM12 20a13 13 0 0 1-1.9-4h3.8A13 13 0 0 1 12 20zm2.3-6H9.7a14 14 0 0 1 0-4h4.6a14 14 0 0 1 0 4zm.3 5.9a15 15 0 0 0 1.3-3.9h3a8 8 0 0 1-4.3 3.9zM16.3 14a16 16 0 0 0 0-4h3.4a8 8 0 0 1 0 4z"/></svg>
        <span>www.brellstone-example.com</span>
      </div>
    </div>
  </section>
</body>
</html>
```